Moxy Fen needs some awesome stationary

Do you have what it takes to get my brand? You either do or you don't, have a crack at a design and you my just win my business.

I don't want to waste your or my time, so put your creative genius on either a business card or envelope.

I however need a package of stationary that follows the same brand. I will message you to complete the remaining should I like your first submission.

Here is what I need, have a go!

Basically I need the following for my small business based in melbourne.
- Letterhead (printer ready and MS Word)
- Business Card
- Compliments Slip
- Envelope
- Proposal Cover Page (MS Word only)
- Presentation Folder
- Marbled Fox Cards
- Student Name Tent
- Index Cards
- Vell-Ka

I am establishing the brand and it must be modern, professional but also relaxed; that is not formal and not corporate. It represents a company are leaders, but small enough to care and operate like a bunch of friends. We are bringing people and conversations back to business, and turfing out all the bureaucracy and crazy and wasteful procedures. Its about "lets talk and figure it out together and find even better ways".

Target Market(s)

Mainly companies that build software products, but Agile practices are used in many other industries (even graphic design projects)

Industry/Entity Type

Information Technology

Font styles to use
Sans Serif

Colors
3176b5
aaaaaa

Requirements
Must have
• I like curves and circles and not boxes or rectangles.
• I want a colour rich design with my brand colours, but it must be balanced.
• I want more modern than traditional, but simple modern
Should not have
• Not corporate
• Please don't waste my time if your not going to think about it.
• Don't mess with my primary logo
• Don't change my colours
• Don't overlay logo on image

```html
<!DOCTYPE html>
<html lang="en">
<head>
<meta charset="utf-8">
<title>Moxy Fen – Marbled Fox card deck</title>
<link rel="stylesheet" href="https://fonts.googleapis.com/css2?family=Ubuntu:wght@400;500;700&display=swap">
<style>
  :root {
    --page: #e2e2e2;
    --brand-blue: #3176b5;
    --brand-grey: #aaaaaa;
    --deck-blue: #3361a8;
    --slate: #6b7175;
    --white: #ffffff;
    --ink: #111111;
    --c-half: #6a2a8a;
    --c-one: #c42a72;
    --c-three: #5bb6ee;
    --c-five: #1d45b0;
    --c-eight: #c2ad12;
    --c-thirteen: #c86f12;
    --c-twenty: #cc2a1e;
    --c-forty: #7e2a2f;
    --c-hundred: #173a32;
    --c-unknown: #111318;
  }
  * { box-sizing: border-box; margin: 0; padding: 0; }
  html, body { width: 1121px; height: 1200px; overflow: hidden; }
  body { background: var(--page); font-family: "Ubuntu", sans-serif; position: relative; }

  .card {
    position: absolute;
    left: var(--x); top: var(--y);
    width: 146px; height: 225px;
    border-radius: 4px;
    background: var(--bg, var(--slate));
    color: var(--white);
    overflow: hidden;
  }
  .card__corner {
    position: absolute; top: 10px; right: 12px;
    font-weight: 700; font-size: 22px; opacity: .85;
  }
  .card__value {
    position: absolute; inset: 0;
    display: flex; align-items: center; justify-content: center;
    font-weight: 700; font-size: 56px; letter-spacing: -1px;
    opacity: .9;
  }
  .card__icon { position: absolute; inset: 0; display: flex; align-items: center; justify-content: center; }

  .card--face { background: var(--white); box-shadow: 1px 2px 3px rgba(0,0,0,.3); }
  .brand-mark { position: absolute; top: 16px; right: 16px; display: flex; align-items: center; gap: 4px; color: var(--brand-blue); font-weight: 700; font-size: 11px; }
  .brand-mark__dot { width: 12px; height: 12px; border-radius: 50%; background: var(--brand-grey); }
  .card--face .card__title { position: absolute; left: 24px; bottom: 14px; color: var(--brand-blue); font-size: 16px; }

  .card--rules { padding: 11px 7px; font-size: 5.6px; line-height: 1.35; }
  .card--rules h3 { font-size: 7.5px; font-weight: 700; margin-bottom: 4px; }
  .card--rules ol { list-style: none; text-align: justify; font-weight: 500; }
  .card--rules dl { display: grid; grid-template-columns: 10px 1fr; gap: 1px 2px; font-weight: 500; }

  .card--back { background: var(--deck-blue); display: flex; flex-direction: column; align-items: center; justify-content: center; gap: 6px; }
  .card--back .back__circle { width: 84px; height: 84px; border-radius: 50%; background: var(--white); margin-bottom: 8px; }
  .card--back .back__name { font-weight: 700; font-size: 24px; }
  .card--back .back__phone { font-weight: 700; font-size: 16px; }
</style>
</head>
<body>

<div class="card card--face" style="--x:64px;--y:126px">
  <div class="brand-mark"><span class="brand-mark__dot"></span>Moxy Fen</div>
  <div class="card__title">Marbled Fox card</div>
</div>
<div class="card" style="--x:226px;--y:127px"><span class="card__corner">0</span><span class="card__value">0</span></div>
<div class="card" style="--x:381px;--y:127px;--bg:var(--c-half)"><span class="card__corner">½</span><span class="card__value">½</span></div>
<div class="card" style="--x:534px;--y:127px;--bg:var(--c-one)"><span class="card__corner">1</span><span class="card__value">1</span></div>
<div class="card" style="--x:691px;--y:126px;--bg:var(--c-three)"><span class="card__corner">3</span><span class="card__value">3</span></div>
<div class="card" style="--x:850px;--y:123px;--bg:var(--c-five)"><span class="card__corner">5</span><span class="card__value">5</span></div>

<div class="card" style="--x:67px;--y:364px;--bg:var(--c-eight)"><span class="card__corner">8</span><span class="card__value">8</span></div>
<div class="card" style="--x:225px;--y:366px;--bg:var(--c-thirteen)"><span class="card__corner">13</span><span class="card__value">13</span></div>
<div class="card" style="--x:384px;--y:358px;--bg:var(--c-twenty)"><span class="card__corner">20</span><span class="card__value">20</span></div>
<div class="card" style="--x:535px;--y:358px;--bg:var(--c-forty)"><span class="card__corner">40</span><span class="card__value">40</span></div>
<div class="card" style="--x:688px;--y:358px;--bg:var(--c-hundred)"><span class="card__corner">100</span><span class="card__value">100</span></div>
<div class="card" style="--x:849px;--y:358px;--bg:var(--c-unknown)"><span class="card__corner">?</span><span class="card__value">?</span></div>

<div class="card" style="--x:63px;--y:602px"><span class="card__corner" style="font-size:26px;top:2px">∞</span><span class="card__value" style="font-size:90px;font-weight:400">∞</span></div>
<div class="card" style="--x:226px;--y:602px">
  <div class="card__icon">
    <svg width="90" height="100" viewBox="0 0 90 100" aria-label="Coffee break">
      <path d="M40 4c-8 8 6 14-2 24M48 10c-5 6 4 10-1 18" stroke="#fff" stroke-width="4" fill="none" stroke-linecap="round"/>
      <path d="M10 42h58l-5 38H17z" fill="#fff"/>
      <path d="M66 50c14-4 16 12 0 16" stroke="#fff" stroke-width="6" fill="none"/>
      <path d="M2 86h80l-10 6H10z" fill="#fff"/>
    </svg>
  </div>
</div>

<svg width="0" height="0" style="position:absolute">
  <defs><path id="tee" d="M34 0q21 12 42 0l34 22-13 19-14-9v60H27V32l-14 9L0 22z" fill="#fff"/></defs>
</svg>

<div class="card" style="--x:380px;--y:602px"><div class="card__icon" style="top:-40px"><svg width="110" height="92"><use href="#tee"/><text x="55" y="66" text-anchor="middle" font-family="Ubuntu, sans-serif" font-weight="700" font-size="20" fill="#111">XS</text></svg></div></div>
<div class="card" style="--x:538px;--y:602px"><div class="card__icon" style="top:-40px"><svg width="110" height="92"><use href="#tee"/><text x="55" y="66" text-anchor="middle" font-family="Ubuntu, sans-serif" font-weight="700" font-size="20" fill="#111">S</text></svg></div></div>
<div class="card" style="--x:694px;--y:602px"><div class="card__icon" style="top:-40px"><svg width="110" height="92"><use href="#tee"/><text x="55" y="66" text-anchor="middle" font-family="Ubuntu, sans-serif" font-weight="700" font-size="20" fill="#111">M</text></svg></div></div>
<div class="card" style="--x:850px;--y:602px"><div class="card__icon" style="top:-40px"><svg width="110" height="92"><use href="#tee"/><text x="55" y="66" text-anchor="middle" font-family="Ubuntu, sans-serif" font-weight="700" font-size="20" fill="#111">L</text></svg></div></div>

<div class="card" style="--x:63px;--y:841px"><div class="card__icon" style="top:10px"><svg width="110" height="92"><use href="#tee"/><text x="55" y="66" text-anchor="middle" font-family="Ubuntu, sans-serif" font-weight="700" font-size="20" fill="#111">XL</text></svg></div></div>
<div class="card" style="--x:227px;--y:841px"><div class="card__icon" style="top:10px"><svg width="110" height="92"><use href="#tee"/><text x="55" y="66" text-anchor="middle" font-family="Ubuntu, sans-serif" font-weight="700" font-size="20" fill="#111">XXL</text></svg></div></div>

<div class="card card--rules" style="--x:390px;--y:841px">
  <h3>Rules</h3>
  <ol>
    <li>1. The Product Owner reads the Product Backlog Item (PBI).</li>
    <li>2. Each developer privately selects the card corresponding to his/her estimate. The estimate should include all activities defined in the Definition of Done.</li>
    <li>3. All developers simultaneously show their cards.</li>
    <li>4. If all developers selected the same value, that becomes the estimate.</li>
    <li>5. If estimates diverge, the two developers whose estimates differ the most explain their point of view.</li>
    <li>6. The estimation procedure is repeated until consensus is reached or agreement that that PBI to be deferred.</li>
  </ol>
  <h3 style="margin-top:6px">Special Cards</h3>
  <dl>
    <dt>0</dt><dd>The product backlog item is already implemented</dd>
    <dt>☕</dt><dd>We should take a break</dd>
    <dt>?</dt><dd>I cannot estimate this product backlog item, I need more information.</dd>
    <dt>∞</dt><dd>The product backlog item is too large.</dd>
  </dl>
</div>

<div class="card card--back" style="--x:546px;--y:842px">
  <span class="back__circle"></span>
  <span class="back__name">Moxy Fen</span>
  <span class="back__phone">13 000 TALKS</span>
</div>
<div class="card card--back" style="--x:703px;--y:842px">
  <span class="back__circle" style="width:100px;height:100px"></span>
  <span class="back__phone">13 000 TALKS</span>
</div>

</body>
</html>
```